Dental Business Card Design w/logo

Classic, elegant w/a touch of contemporary
Upscale dental facility located in Modesto CA
Specializing in restorative & general dentistry
Providing exceptional customer service to the community
Updates

I prefer script and not bold writing
If you can use the phone; fax and email icons instead of spelling them out, it would be great
No bold colors
Classy and elegant
In the back of the card I would like to see something like this
Your Next Appointment:
Mon     Tue    Wed    Thur (a box next to each of them for marking)
Date:_______________ at_____________ AM    PM  (a box next to them for marking)

Thank you

Target Market(s)

Well established professional

Industry/Entity Type

Dental

Contact Information for Business Card

Velarina Tossudi DMD
4176 Marlow Rd
Suite K7
Modesto, CA 95418

Office: 209-731-5920
Fax: 209-731-8047
Email: tossudidmd@quillmail.example

Requirements
Must have
• Unique classic logo
An easily repeatable design that can be used on letterhead and envelopes
Nice to have
• My initials incorporated into unique design
Should not have
• No cartoons or cheesy themes. This is a practice for the well established and professional individual.

```html
<!DOCTYPE html>
<html lang="en">
<head>
<meta charset="UTF-8">
<title>Velarina Tossudi DMD — Business Card</title>
<link rel="stylesheet" href="https://fonts.googleapis.com/css2?family=Roboto+Condensed:wght@700&family=Jost:wght@300;400&display=swap">
<style>
  :root {
    --page: #ffffff;
    --card: #ffffff;
    --card-edge: #1a1a1a;
    --band: #a8d987;
    --mark: #a8d987;
    --slate: #5e6b75;
    --ink: #000000;
    --text: #2e2e2e;
  }
  * { margin: 0; padding: 0; box-sizing: border-box; }
  html, body {
    width: 1200px;
    height: 900px;
    overflow: hidden;
    background: var(--page);
  }
  .card {
    position: absolute;
    left: 118px;
    top: 169px;
    width: 969px;
    height: 572px;
    background: var(--card);
    border: 1px solid var(--card-edge);
    overflow: hidden;
  }
  .brand {
    position: absolute;
    left: 92px;
    top: 40px;
    width: 228px;
    text-align: right;
  }
  .brand-dot {
    display: block;
    width: 120px;
    height: 120px;
    margin: 0 52px 14px auto;
    border-radius: 50%;
    background: var(--mark);
  }
  .brand-name {
    font-family: "Roboto Condensed", sans-serif;
    font-weight: 700;
    color: var(--slate);
    font-size: 40px;
    line-height: 44px;
    letter-spacing: 1px;
    text-transform: uppercase;
  }
  .person {
    position: absolute;
    right: 59px;
    top: 112px;
    text-align: right;
  }
  .person-name {
    font-family: "Roboto Condensed", sans-serif;
    font-weight: 700;
    color: var(--ink);
    font-size: 58px;
    line-height: 58px;
    letter-spacing: 1px;
    text-transform: uppercase;
  }
  .person-title {
    font-family: "Jost", sans-serif;
    font-weight: 300;
    color: var(--slate);
    font-size: 36px;
    line-height: 40px;
    margin-top: 2px;
  }
  .contact-band {
    position: absolute;
    left: 0;
    bottom: 0;
    width: 100%;
    height: 181px;
    background: var(--band);
  }
  .contact {
    position: absolute;
    right: 59px;
    top: 30px;
    text-align: right;
    font-family: "Jost", sans-serif;
    font-weight: 400;
    color: var(--text);
    font-size: 25px;
    line-height: 32px;
    font-style: normal;
  }
</style>
</head>
<body>
  <main class="card">
    <div class="brand">
      <span class="brand-dot" aria-hidden="true"></span>
      <p class="brand-name">Velarina<br>Tossudi<br>Dentistry</p>
    </div>

    <div class="person">
      <h1 class="person-name">Velarina<br>Tossudi</h1>
      <p class="person-title">DMD</p>
    </div>

    <section class="contact-band">
      <address class="contact">
        <p>4176 Marlow Rd Suite K7 Modesto, CA 95418</p>
        <p>OFFICE: 209-731-5920 FAX: 209-731-8047</p>
        <p>EMAIL: tossudidmd@quillmail.example</p>
      </address>
    </section>
  </main>
</body>
</html>
```